2022 Yearly Patron Drive (art gallery annual report)

6X9, 16-page brochure that serves both as an annual report for the previous year and gets mailed for an ask for donations. This must be done in InDesign and I will provide a template. I am also sending PDFs for the previous two years. Last year was pink and black, but I have recolored the logo purple this year.. so am open to whatever colors. I used last year's template to put in the new info. The theme for this year is Amazing - last year was Thriving. The font I chose for the front I do not want to use.. its just an example. All three pictures on the front don't have to be used.. just ideas.
Updates

I put three photos on the front page. It isn't necessary to use all of them, I thought there might be something there to use as part of the design

The current information is in the InDesign file, Calatalog Design.indd with the to Links Folders attached.

Target Market(s)

Donors

Industry/Entity Type

Art

Font styles to use
Sans Serif

Requirements
Must have
• InDesign
Nice to have
• A new look! Something different than 2021 an 2020 (PDFs included)

```html
<!DOCTYPE html>
<html lang="en">
<head>
<meta charset="utf-8">
<title>Activities – Yearly Patron Drive 2022</title>
<link rel="stylesheet" href="https://fonts.googleapis.com/css2?family=Oswald:wght@600&family=Open+Sans:wght@400;700&family=DM+Serif+Display&display=swap">
<style>
  :root {
    --page-bg: #ffffff;
    --brand-ink: #111111;
    --accent-orange: #f47a20;
    --accent-pink: #e6198a;
    --body-grey: #606060;
    --footer-pill: #3c3a4e;
    --theme-wine: #6e2a42;
    --rule: #222222;
    --photo-red: #c8141f;
    --photo-white: #ece8e4;
  }
  html, body {
    margin: 0;
    padding: 0;
    width: 1200px;
    height: 800px;
    overflow: hidden;
    background: var(--page-bg);
  }
  .page {
    position: relative;
    width: 1200px;
    height: 800px;
    overflow: hidden;
    font-family: "Open Sans", sans-serif;
  }
  .brand-name {
    position: absolute;
    left: 54px;
    top: 50px;
    margin: 0;
    font-family: "Open Sans", sans-serif;
    font-weight: 700;
    font-size: 30px;
    letter-spacing: 5px;
    color: var(--brand-ink);
    line-height: 1;
  }
  .section-title {
    position: absolute;
    left: 108px;
    top: 144px;
    margin: 0;
    font-family: "Oswald", sans-serif;
    font-weight: 600;
    font-size: 66px;
    line-height: 1;
    color: var(--accent-orange);
    letter-spacing: -0.5px;
  }
  .report-body {
    position: absolute;
    left: 110px;
    top: 248px;
    width: 706px;
    color: var(--body-grey);
    font-size: 18.2px;
    line-height: 23.7px;
  }
  .report-body p {
    margin: 0 0 23.7px;
    text-align: justify;
  }
  .event-photo {
    position: absolute;
    left: 853px;
    top: 132px;
    width: 280px;
    height: 521px;
    background: linear-gradient(135deg, var(--photo-red) 0%, var(--photo-white) 45%, var(--photo-red) 100%);
  }
  .photo-caption {
    position: absolute;
    left: 853px;
    top: 670px;
    width: 280px;
    margin: 0;
    text-align: center;
    font-size: 19px;
    color: var(--brand-ink);
  }
  .photo-caption .dash { color: var(--accent-pink); }
  .page-footer .page-number {
    position: absolute;
    left: 0;
    top: 739px;
    width: 55px;
    height: 25px;
    background: var(--footer-pill);
    border-radius: 0 13px 13px 0;
    color: #ffffff;
    font-weight: 700;
    font-size: 14px;
    line-height: 25px;
    text-align: right;
    box-sizing: border-box;
    padding-right: 16px;
  }
  .page-footer .theme-word {
    position: absolute;
    left: 67px;
    top: 733px;
    margin: 0;
    font-family: "DM Serif Display", serif;
    font-size: 26px;
    line-height: 1;
    color: var(--theme-wine);
  }
  .page-footer .footer-rule {
    position: absolute;
    left: 189px;
    top: 753px;
    width: 1011px;
    height: 1px;
    background: var(--rule);
  }
</style>
</head>
<body>
<main class="page">
  <p class="brand-name">MARLOW</p>

  <h1 class="section-title">ACTIVITIES</h1>

  <section class="report-body">
    <p>In 2022, we hosted several notable events. We welcomed back our annual Marlow Gallery Guild membership event. This year it was held at Cedar Hollow Brewing Co. with food catered by Auntie Rose.</p>
    <p>Several of our events involve our new neighbors--Riverbend Vintners, who have been a partner for events like Art After Hours at the Marlow Gallery. Guests were able to enjoy delicious wines created by Riverbend Valley College students. The Vintners tasting room is also open on Fridays and Saturdays of each month, between 12-5:00 and on the last Friday of the month offers extended hours until 7 pm.&nbsp; Wine, art, and cheese plates--all under one roof. What a great way to end your work weeks and join us.</p>
    <p>We finished the year by welcoming Santa to our decked-out&nbsp; halls.&nbsp; Our pint-sized Marlow Guild supporters enjoyed miniature stockings filled with candy as they waited to tell Santa what they hoped he would bring them for Christmas.</p>
  </section>

  <div class="event-photo" role="img" aria-label="Photo of Santa Claus greeting a baby in a red Santa hat at the holiday event"></div>
  <p class="photo-caption"><span class="dash">-</span> Santa Claus <span class="dash">-</span></p>

  <footer class="page-footer">
    <div class="page-number">8</div>
    <p class="theme-word">Amazing</p>
    <div class="footer-rule"></div>
  </footer>
</main>
</body>
</html>
```